Oral Surgeon Referral Pads

Hello. We need referral pads for Dr Elsabet Quorvane, DDS board certified oral surgeon's new office - Harrowgate Dunmere Oral & Maxillofacial Surgery. See logo uploaded. See some images we would like included
Updates

Designs look the same

Font styles to use
Serif
Script

Colors
00AB8E
00BBA5
67D7C9
C6EFE9
E9F9F6

Requirements
Must have
• Color Pantone 623c. Also foldable business cards

```html
<!DOCTYPE html>
<html lang="en">
<head>
<meta charset="utf-8">
<title>Harrowgate Dunmere Oral &amp; Maxillofacial Surgery – Referral Pad</title>
<link href="https://fonts.googleapis.com/css2?family=Open+Sans:wght@400;600&display=swap" rel="stylesheet">
<style>
  :root {
    --navy: #233066;
    --paper: #ffffff;
    --backdrop: #626262;
    --ink: #2a2a3a;
  }
  * { box-sizing: border-box; margin: 0; padding: 0; }
  html, body {
    width: 1200px; height: 1004px; overflow: hidden;
    background: var(--backdrop);
    font-family: "Open Sans", Arial, sans-serif;
  }
  .pad-frame {
    position: absolute; left: 257px; top: 22px;
    width: 686px; height: 960px;
  }
  .pad {
    position: absolute; left: 0; top: 0;
    width: 823px; height: 1152px;
    background: var(--paper);
    transform: scale(0.8333); transform-origin: 0 0;
    color: var(--navy);
  }
  .brand {
    position: absolute; left: 40px; top: 48px; width: 260px;
    display: flex; flex-direction: column; align-items: center; text-align: center;
  }
  .brand-mark {
    width: 34px; height: 34px; border-radius: 50%;
    background: var(--navy); margin-bottom: 12px;
  }
  .brand-name {
    font-size: 20px; font-weight: 600; line-height: 1.25; color: var(--navy);
  }
  .contact {
    position: absolute; left: 532px; top: 27px; list-style: none;
    font-size: 15px; line-height: 21.6px; color: var(--ink);
  }
  .contact li { display: flex; align-items: center; gap: 4px; }
  .contact svg { width: 13px; height: 13px; fill: var(--navy); flex: none; }
  .referral-band {
    position: absolute; left: 46px; top: 176px; width: 732px; height: 121px;
    background: var(--navy); border-radius: 28px; overflow: hidden;
  }
  .referral-band .divider {
    position: absolute; left: 0; right: 0; top: 59px; height: 3px; background: var(--paper);
  }
  .field-label {
    position: absolute; color: var(--paper); font-size: 15px; letter-spacing: 0.2px;
  }
  .panel {
    position: absolute; left: 47px; width: 729px;
    border: 2px solid var(--navy); border-radius: 22px;
  }
  .panel-title {
    position: absolute; left: 250px; top: -19px; width: 226px; height: 37px;
    background: var(--navy); color: var(--paper);
    font-size: 21px; display: flex; align-items: center; justify-content: center;
  }
  .treatment-panel { top: 341px; height: 237px; }
  .treatment-list {
    position: absolute; top: 36px; list-style: none;
    font-size: 16px; line-height: 24.7px; color: var(--ink);
  }
  .treatment-list li { display: flex; align-items: center; gap: 6px; white-space: nowrap; }
  .treatment-list li::before {
    content: ""; width: 11px; height: 11px; border: 1.5px solid var(--navy); border-radius: 2px;
  }
  .tooth-chart { position: absolute; left: 0; top: 590px; }
  .tooth-chart text { font-family: "Open Sans", Arial, sans-serif; font-size: 18px; fill: var(--ink); text-anchor: middle; }
  .notes {
    position: absolute; left: 53px; top: 757px; width: 720px;
    font-size: 18.5px; line-height: 29.8px; color: var(--ink);
  }
  .comments-panel { top: 953px; height: 175px; }
  .write-line {
    position: absolute; left: 30px; right: 30px; height: 1.5px; background: var(--navy);
  }
</style>
</head>
<body>
<div class="pad-frame">
  <article class="pad">
    <header>
      <div class="brand">
        <span class="brand-mark"></span>
        <div class="brand-name">Harrowgate Dunmere<br>Oral &amp; Maxillofacial Surgery</div>
      </div>
      <ul class="contact">
        <li><svg viewBox="0 0 12 12"><path d="M6 0a4 4 0 0 0-4 4c0 3 4 8 4 8s4-5 4-8a4 4 0 0 0-4-4zm0 5.5a1.5 1.5 0 1 1 0-3 1.5 1.5 0 0 1 0 3z"/></svg>Your address, City State, Zip 1234</li>
        <li><svg viewBox="0 0 12 12"><path d="M2.5 0.5l2 2.5-1.2 1.5c.8 1.6 2.1 2.9 3.7 3.7L8.5 7l2.5 2-1.5 2.5C4.8 11 1 7.2.5 2.5z"/></svg>123 456 789</li>
        <li><svg viewBox="0 0 12 12"><path d="M1 4h10v8H1zM3 0h6v3H3z"/></svg>123 456 789</li>
        <li><svg viewBox="0 0 12 12"><path d="M0 3h12v8H0zm1 1l5 3.5L11 4z"/></svg>info@yourgmail.com</li>
        <li><svg viewBox="0 0 12 12"><circle cx="6" cy="6" r="6"/></svg>www.yourwebsite.com</li>
      </ul>
    </header>

    <section class="referral-band">
      <span class="field-label" style="left:35px;top:18px">INTRODUCING</span>
      <span class="field-label" style="left:487px;top:18px">DATE</span>
      <div class="divider"></div>
      <span class="field-label" style="left:35px;top:80px">REFFERRED BY</span>
      <span class="field-label" style="left:487px;top:80px">PHONE</span>
    </section>

    <section class="panel treatment-panel">
      <h2 class="panel-title" style="font-weight:400">Evaluate/Treat</h2>
      <ul class="treatment-list" style="left:21px">
        <li>Wisdom Teeth</li><li>Extraction</li><li>Implants</li><li>Bone Grafing</li>
        <li>Exposure and bonding</li><li>Biopsy(SOFT or Hard Tissue)</li><li>Connectivee Tissue Graft</li>
      </ul>
      <ul class="treatment-list" style="left:258px">
        <li>Wisdom Teeth</li><li>Extraction</li><li>Implants</li><li>Bone Grafing</li>
        <li>Exposure and bonding</li><li>Biopsy(SOFT or Hard Tissue)</li><li>Connectivee Tissue Graft</li>
      </ul>
      <ul class="treatment-list" style="left:489px">
        <li>Wisdom Teeth</li><li>Extraction</li><li>Implants</li><li>Bone Grafing</li>
        <li>Exposure and bonding</li><li>Biopsy(SOFT or Hard Tissue)</li><li>Connectivee Tissue Graft</li>
      </ul>
    </section>

    <svg class="tooth-chart" width="823" height="150" viewBox="0 590 823 150" aria-label="Tooth chart">
      <line x1="420" y1="608" x2="420" y2="722" stroke="#233066" stroke-width="2"/>
      <line x1="45" y1="665" x2="778" y2="665" stroke="#233066" stroke-width="2"/>
      <g>
        <text x="100" y="623">1</text><text x="134" y="623">2</text><text x="172" y="623">3</text><text x="211" y="623">4</text><text x="249" y="623">5</text><text x="287" y="623">6</text><text x="324" y="623">7</text><text x="362" y="623">8</text><text x="399" y="623">9</text>
        <text x="442" y="623">10</text><text x="488" y="623">11</text><text x="534" y="623">12</text><text x="581" y="623">13</text><text x="628" y="623">14</text><text x="677" y="623">15</text><text x="723" y="623">16</text>
      </g>
      <g>
        <text x="249" y="653">A</text><text x="287" y="653">B</text><text x="324" y="653">C</text><text x="362" y="653">D</text><text x="399" y="653">E</text>
        <text x="442" y="653">F</text><text x="488" y="653">G</text><text x="534" y="653">H</text><text x="581" y="653">I</text>
      </g>
      <g>
        <text x="249" y="690">T</text><text x="287" y="690">S</text><text x="324" y="690">R</text><text x="362" y="690">Q</text><text x="399" y="690">P</text>
        <text x="442" y="690">O</text><text x="488" y="690">N</text><text x="534" y="690">M</text><text x="581" y="690">L</text>
        <text x="628" y="690">14</text><text x="677" y="690">15</text><text x="723" y="690">16</text>
      </g>
      <g>
        <text x="100" y="721">32</text><text x="134" y="721">31</text><text x="172" y="721">30</text><text x="211" y="721">29</text><text x="249" y="721">28</text><text x="287" y="721">27</text><text x="324" y="721">26</text><text x="362" y="721">25</text><text x="399" y="721">24</text>
        <text x="442" y="721">23</text><text x="488" y="721">22</text><text x="534" y="721">21</text><text x="581" y="721">20</text><text x="628" y="721">19</text><text x="677" y="721">18</text><text x="723" y="721">17</text>
      </g>
    </svg>

    <p class="notes">Lorem Ipsum is simply dummy text of the printing and typesetting industry. Lorem Ipsum has been the industry's standard dummy text ever since the 1500s, when an unknown printer took a galley of type and scrambled it to make a type specimen book. It has survived not only five centuries, but also the leap into electronic type-setting, remaining essentially unchanged. It was popularised in the 1960s with the</p>

    <section class="panel comments-panel">
      <h2 class="panel-title" style="font-weight:400">COMMENTS</h2>
      <div class="write-line" style="top:55px"></div>
      <div class="write-line" style="top:98px"></div>
      <div class="write-line" style="top:140px"></div>
    </section>
  </article>
</div>
</body>
</html>
```